Web Developer Needs a Business Card Design

I need a personal business card design that represents me as a web developer for potential employers. I would like the background to be a dark color on the front for contrast with my logo and name. The back will have all my information along with a smaller version of the logo. I want something with a modern look and feel, not too conservative. This will be used for potential employers and freelance work.

Industry/Entity Type

Business

Contact Information for Business Card

Front should have my logo and name. The back should have all my personal information which would include: name: Tom Varulek, phone: 570-614-3098, email: tomvarulek@quillbox.net, website url: www.tomvarulek.net, logo, web developer.

Font styles to use
Sans Serif

Requirements
Must have
• Must include my logo. The color palette base color will be the logo color.

```html
<!DOCTYPE html>
<html lang="en">
<head>
<meta charset="utf-8">
<title>Tom Varulek — Business Card</title>
<link rel="stylesheet" href="https://fonts.googleapis.com/css2?family=Open+Sans:wght@400;600&display=swap">
<style>
  :root {
    --backdrop: #e9e7e3;
    --card-white: #f4f4f4;
    --brand-teal: #66b9a8;
    --ink: #111111;
    --icon-fg: #ffffff;
  }
  html, body {
    margin: 0;
    width: 1200px;
    height: 902px;
    overflow: hidden;
    background: var(--backdrop);
    font-family: "Open Sans", sans-serif;
  }
  .business-card {
    position: absolute;
    left: 100px;
    top: 165px;
    width: 1000px;
    height: 572px;
    background: var(--card-white);
    box-shadow: 0 12px 30px rgba(0,0,0,0.18);
    overflow: hidden;
  }
  .card-shapes {
    position: absolute;
    inset: 0;
  }
  .brand-mark {
    position: absolute;
    left: 40px;
    top: 250px;
    width: 320px;
    display: flex;
    align-items: center;
    justify-content: center;
    gap: 14px;
    color: var(--brand-teal);
    font-weight: 600;
    font-size: 44px;
    line-height: 1;
  }
  .brand-dot {
    width: 28px;
    height: 28px;
    border-radius: 50%;
    background: var(--brand-teal);
    flex: none;
  }
  .identity {
    position: absolute;
    right: 48px;
    top: 46px;
    text-align: right;
    color: var(--ink);
  }
  .identity-name {
    margin: 0;
    font-weight: 400;
    font-size: 64px;
    line-height: 1;
    letter-spacing: 0.5px;
  }
  .identity-role {
    margin: 4px 0 0;
    font-size: 28px;
    line-height: 1;
  }
  .contact-list {
    position: absolute;
    right: 48px;
    bottom: 70px;
    margin: 0;
    padding: 0;
    list-style: none;
    color: var(--ink);
    font-size: 27px;
    line-height: 1;
  }
  .contact-item {
    display: flex;
    justify-content: flex-end;
    align-items: center;
    gap: 18px;
    margin-top: 14px;
  }
  .contact-icon {
    width: 24px;
    height: 24px;
    background: var(--ink);
    flex: none;
    display: block;
  }
</style>
</head>
<body>
  <main class="business-card">
    <svg class="card-shapes" width="1000" height="572" viewBox="0 0 1000 572" aria-hidden="true">
      <path d="M310 0 C 420 120, 470 330, 440 572 L 1000 572 L 1000 0 Z" fill="var(--ink)"/>
      <path d="M330 0 C 440 120, 492 330, 462 572 L 1000 572 L 1000 0 Z" fill="var(--brand-teal)"/>
    </svg>

    <div class="brand-mark">
      <span class="brand-dot"></span>
      <span>Varulek</span>
    </div>

    <header class="identity">
      <h1 class="identity-name">Tom Varulek</h1>
      <p class="identity-role">web developer</p>
    </header>

    <ul class="contact-list">
      <li class="contact-item">
        <span>570-614-3098</span>
        <svg class="contact-icon" viewBox="0 0 24 24" aria-label="phone">
          <rect width="24" height="24" fill="var(--ink)"/>
          <path d="M8 5 L10 5 L11 9 L9.5 10.5 C10.5 12.5 11.5 13.5 13.5 14.5 L15 13 L19 14 L19 16 C19 17.5 17.5 19 16 19 C10 18.5 5.5 14 5 8 C5 6.5 6.5 5 8 5 Z" fill="var(--icon-fg)"/>
        </svg>
      </li>
      <li class="contact-item">
        <span>www.tomvarulek.net</span>
        <svg class="contact-icon" viewBox="0 0 24 24" aria-label="website">
          <rect width="24" height="24" fill="var(--ink)"/>
          <circle cx="12" cy="12" r="7" fill="none" stroke="var(--icon-fg)" stroke-width="1.6"/>
          <ellipse cx="12" cy="12" rx="3" ry="7" fill="none" stroke="var(--icon-fg)" stroke-width="1.4"/>
          <line x1="5" y1="12" x2="19" y2="12" stroke="var(--icon-fg)" stroke-width="1.4"/>
        </svg>
      </li>
      <li class="contact-item">
        <span>tomvarulek@quillbox.net</span>
        <svg class="contact-icon" viewBox="0 0 24 24" aria-label="email">
          <rect width="24" height="24" fill="var(--ink)"/>
          <rect x="5" y="7" width="14" height="10" fill="none" stroke="var(--icon-fg)" stroke-width="1.6"/>
          <path d="M5 7 L12 13 L19 7" fill="none" stroke="var(--icon-fg)" stroke-width="1.6"/>
        </svg>
      </li>
    </ul>
  </main>
</body>
</html>
```